Vantiqo custom business card design

Need a authentic, innovative business card design for a new mobile app business. I am uploading a few screen images from our app for you to view. I would like app design theme to match business card design. I can also send logo images.

```html
<!DOCTYPE html>
<html lang="en">
<head>
<meta charset="UTF-8">
<title>Vantiqo Business Card</title>
<link rel="stylesheet" href="https://fonts.googleapis.com/css2?family=Work+Sans:wght@400;500;800&display=swap">
<style>
  :root {
    --purple: #622d8c;
    --ink: #1e1e1e;
    --paper: #ffffff;
    --backdrop: #b9b9b9;
    --text: #2a2a2a;
  }
  * { margin: 0; padding: 0; box-sizing: border-box; }
  html, body { width: 1200px; height: 930px; overflow: hidden; }
  body {
    background: var(--backdrop);
    font-family: "Work Sans", sans-serif;
    position: relative;
  }
  .card {
    position: absolute;
    width: 620px;
    height: 354px;
    border-radius: 24px;
    overflow: hidden;
    box-shadow: 0 6px 18px rgba(0,0,0,0.25);
  }
  .card-front {
    left: 80px; top: 80px;
    background: var(--purple);
    display: flex; align-items: center; justify-content: center;
  }
  .brand { display: flex; flex-direction: column; align-items: center; gap: 14px; }
  .brand-mark { width: 96px; height: 96px; border-radius: 50%; background: var(--paper); }
  .brand-name { font-weight: 800; font-size: 44px; color: var(--paper); letter-spacing: 0.5px; }

  .card-back { left: 500px; top: 500px; background: var(--paper); }
  .back-brand { position: absolute; left: 56px; top: 40px; display: flex; flex-direction: column; align-items: flex-start; gap: 8px; }
  .back-brand .brand-mark { width: 82px; height: 82px; background: var(--purple); margin-left: 18px; }
  .back-brand .brand-name { color: var(--ink); font-size: 34px; }

  .holder { position: absolute; right: 40px; top: 78px; text-align: right; }
  .holder-name { color: var(--purple); font-weight: 500; font-size: 25px; letter-spacing: 0.3px; }
  .holder-role { color: var(--text); font-size: 14px; margin-top: 2px; }

  .divider { position: absolute; left: 56px; right: 40px; top: 178px; height: 1.5px; background: var(--purple); }

  .contacts { position: absolute; left: 58px; top: 194px; list-style: none; z-index: 1; }
  .contacts li { display: flex; align-items: center; gap: 12px; font-size: 16px; color: var(--text); height: 23px; }
  .contacts svg { width: 13px; height: 13px; flex: none; }

  .address { position: absolute; right: 40px; top: 190px; text-align: right; font-size: 15px; color: var(--text); line-height: 22px; z-index: 1; }

  .wave { position: absolute; left: 0; bottom: 0; width: 620px; height: 354px; }
</style>
</head>
<body>
  <section class="card card-front">
    <div class="brand">
      <div class="brand-mark"></div>
      <div class="brand-name">Vantiqo</div>
    </div>
  </section>

  <section class="card card-back">
    <svg class="wave" viewBox="0 0 620 354" aria-hidden="true">
      <path d="M0 354 L0 346 C140 344 230 326 330 292 C430 258 520 248 620 244 L620 354 Z" fill="#111"/>
      <path d="M0 354 L0 350 C150 348 240 331 335 298 C435 264 525 255 620 251 L620 354 Z" fill="#fff"/>
      <path d="M0 354 C170 353 250 336 340 303 C440 268 530 259 620 256 L620 354 Z" fill="#622d8c"/>
    </svg>

    <div class="back-brand">
      <div class="brand-mark"></div>
      <div class="brand-name">Vantiqo</div>
    </div>

    <div class="holder">
      <div class="holder-name">DANIEL REYES</div>
      <div class="holder-role">Director</div>
    </div>

    <div class="divider"></div>

    <ul class="contacts">
      <li><svg viewBox="0 0 14 14"><rect x="3.5" y="1" width="7" height="12" rx="1.2" fill="none" stroke="#622d8c" stroke-width="1.4"/></svg>(555) 410-2287</li>
      <li><svg viewBox="0 0 14 14"><path d="M3 1.5 L5.5 4 L4.2 5.6 C5 7.5 6.5 9 8.4 9.8 L10 8.5 L12.5 11 L11 12.5 C6 12 2 8 1.5 3 Z" fill="#622d8c"/></svg>(555) 738-6094</li>
      <li><svg viewBox="0 0 14 14"><rect x="1" y="3" width="12" height="8" fill="none" stroke="#622d8c" stroke-width="1.3"/><path d="M1 3 L7 8 L13 3" fill="none" stroke="#622d8c" stroke-width="1.3"/></svg>info@Vantiqo.com</li>
      <li><svg viewBox="0 0 14 14"><circle cx="7" cy="7" r="6" fill="none" stroke="#622d8c" stroke-width="1.2"/><path d="M1 7 H13 M7 1 C4 4 4 10 7 13 M7 1 C10 4 10 10 7 13" fill="none" stroke="#622d8c" stroke-width="1"/></svg>www.Vantiqo.com</li>
    </ul>

    <div class="address">
      2741 Harbor Lane<br>
      Marlow Bay, FL 30218
    </div>
  </section>
</body>
</html>
```